Print Ad for a Human Resource Company

Hi.
Apologies for the quick turnaround but I just was brought on board to handle this project. The publication is Harbor Crest Journal, a Hawaii Business & Lifestyle publication.
Their upcoming issue will feature HR companies & of course we want our ad to stand out from the rest & make the phone ring.

Size: Vertical Ad 2.5" x 9.875

Color: 4 color, non bleed

Format: Hi-res (300 dpi) pdf
Ad Due: Drop dead dealine is Friday, 1/04/2013

Color: 4 color, non bleed

Reason: There is a God in heaven. We have a stay on the deadline to January 4th.

Target Market(s)

Small companies that benefit from having experts handle these areas.

Industry/Entity Type

Business

Requirements
Must have
• Copy:
Tagline: Keeping It Simple
Accounting
Human Resources
Payroll Services
Employee Benefits
Commercial Insurance
Personal Insurance
No Hidden Fees

Photos of both owners:
Marisol Ventanilla, CEO
Kara Whitlow, President

Company logo
Address: 512 Coral Mill Service Lane, Suite #214
Makani Falls, HI 96799
Phone: 808.555.3172
BrightLedgerHelp.example
Nice to have
• This is a small locally owned firm owned by 2 local, very smart, sophisticated yet approachable, hardworking women. Their colors are Black background, silver type. The ad should be a reflection of their personalities.

```html
<!DOCTYPE html>
<html lang="en">
<head>
<meta charset="utf-8">
<title>BrightLedger – Vertical Print Ad</title>
<link href="https://fonts.googleapis.com/css2?family=Open+Sans:wght@400;600;700&family=Arimo:wght@400&family=Yesteryear&display=swap" rel="stylesheet">
<style>
  :root {
    --page: #ffffff;
    --ad-black: #050505;
    --silver: #e6e6e6;
    --white: #ffffff;
    --ghost: #2f2c2c;
    --gold-tick: #c9bb4c;
    --label-grey: #8a8a8a;
    --contact-grey: #b5b5b5;
    --band-dark: #151515;
    --band-mid: #2a2a2a;
    --portrait-light: #9a9a9a;
    --portrait-dark: #2b2b2b;
  }
  * { margin: 0; padding: 0; box-sizing: border-box; }
  html, body {
    width: 1200px; height: 1000px; overflow: hidden;
    background: var(--page);
  }
  .ad {
    position: absolute; left: 477px; top: 8px;
    width: 249px; height: 983px;
    background: var(--ad-black);
    font-family: "Open Sans", Arial, sans-serif;
    overflow: hidden;
  }
  .brand-name {
    position: absolute; right: 33px; top: 24px;
    font-weight: 700; font-size: 20.5px; letter-spacing: 0.5px;
    color: var(--white);
  }
  .tagline {
    position: absolute; right: 33px; top: 54px;
    font-weight: 600; font-size: 14px;
    color: var(--white);
  }
  .brand-ghost {
    position: absolute; left: 0; width: 100%; top: 86px;
    text-align: center;
    font-weight: 700; font-size: 27.5px; letter-spacing: 0;
    color: var(--ghost);
  }
  .services {
    position: absolute; left: 24px; top: 160px;
    list-style: none;
  }
  .services li {
    display: flex; align-items: center;
    height: 25px;
    font-family: "Yesteryear", "Brush Script MT", cursive;
    font-size: 20px; color: var(--silver);
    letter-spacing: 1.3px;
  }
  .services svg { width: 14px; height: 14px; margin-right: 6px; flex: none; }
  .leader {
    position: absolute; left: 0; width: 100%;
  }
  .leader-band {
    position: absolute; left: 10px; right: 12px; height: 88px;
    background: linear-gradient(90deg, var(--ad-black) 0%, var(--band-mid) 30%, var(--band-dark) 50%, var(--band-mid) 70%, var(--ad-black) 100%);
  }
  .portrait {
    position: absolute; left: 65px; width: 120px; height: 150px;
    background: radial-gradient(ellipse at 50% 35%, var(--portrait-light) 0%, #5c5c5c 55%, var(--portrait-dark) 100%);
  }
  .leader-name, .leader-role {
    position: absolute; left: 0; width: 100%;
    text-align: center;
    font-family: "Arimo", Arial, sans-serif;
    font-size: 14px; color: var(--label-grey);
  }
  .contact-heading {
    position: absolute; left: 17px; top: 828px;
    font-size: 14.5px; color: var(--contact-grey);
  }
  .contact-line {
    position: absolute; left: 17px;
    font-size: 10.5px; line-height: 15px; color: var(--silver);
    white-space: nowrap;
  }
  .brand-foot {
    position: absolute; right: 13px; top: 959px;
    font-weight: 700; font-size: 10px; letter-spacing: 0.3px;
    color: var(--white);
  }
</style>
</head>
<body>
  <div class="ad">
    <div class="brand-name">BRIGHTLEDGER</div>
    <div class="tagline">Keeping It Simple</div>
    <div class="brand-ghost">BRIGHTLEDGER</div>

    <ul class="services">
      <li><svg viewBox="0 0 14 14"><path d="M2 7.5 L5.5 11 L12.5 2.5" fill="none" stroke="var(--gold-tick)" stroke-width="2.4" stroke-linecap="round"/></svg>Accounting</li>
      <li><svg viewBox="0 0 14 14"><path d="M2 7.5 L5.5 11 L12.5 2.5" fill="none" stroke="var(--gold-tick)" stroke-width="2.4" stroke-linecap="round"/></svg>Human Resources</li>
      <li><svg viewBox="0 0 14 14"><path d="M2 7.5 L5.5 11 L12.5 2.5" fill="none" stroke="var(--gold-tick)" stroke-width="2.4" stroke-linecap="round"/></svg>Payroll Services</li>
      <li><svg viewBox="0 0 14 14"><path d="M2 7.5 L5.5 11 L12.5 2.5" fill="none" stroke="var(--gold-tick)" stroke-width="2.4" stroke-linecap="round"/></svg>Employee Benefits</li>
      <li><svg viewBox="0 0 14 14"><path d="M2 7.5 L5.5 11 L12.5 2.5" fill="none" stroke="var(--gold-tick)" stroke-width="2.4" stroke-linecap="round"/></svg>Commercial Insurance</li>
      <li><svg viewBox="0 0 14 14"><path d="M2 7.5 L5.5 11 L12.5 2.5" fill="none" stroke="var(--gold-tick)" stroke-width="2.4" stroke-linecap="round"/></svg>Personal Insurance</li>
      <li><svg viewBox="0 0 14 14"><path d="M2 7.5 L5.5 11 L12.5 2.5" fill="none" stroke="var(--gold-tick)" stroke-width="2.4" stroke-linecap="round"/></svg>No Hidden Fees</li>
    </ul>

    <div class="leader">
      <div class="leader-band" style="top:424px"></div>
      <div class="portrait" style="top:394px" role="img" aria-label="Portrait photo of Kara Whitlow, President"></div>
      <div class="leader-name" style="top:554px">Kara Whitlow</div>
      <div class="leader-role" style="top:572px">PRESIDENT</div>
    </div>

    <div class="leader">
      <div class="leader-band" style="top:628px"></div>
      <div class="portrait" style="top:606px" role="img" aria-label="Portrait photo of Marisol Ventanilla, CEO"></div>
      <div class="leader-name" style="top:766px">Marisol Ventanilla</div>
      <div class="leader-role" style="top:784px">CEO</div>
    </div>

    <div class="contact-heading">Contact Us</div>
    <div class="contact-line" style="top:856px">512 Coral Mill Service Lane, Suite #214<br>Makani Falls, HI 96799</div>
    <div class="contact-line" style="top:901px">Phone: 808.555.3172</div>
    <div class="contact-line" style="top:931px">BrightLedgerHelp.example</div>

    <div class="brand-foot">BRIGHTLEDGER</div>
  </div>
</body>
</html>
```